Rollers & Glides.com

Vertical Business Card with focus on branding with our icon. Information on card will be logo, persons name, position, phone number, email address and website. Use the the name Marcus Pellow, position President, phone number 480.915.2267, email Marcus@rollersandglides-demo.com, website www.rollersandglides-demo.com.

```html
<!DOCTYPE html>
<html lang="en">
<head>
<meta charset="utf-8">
<title>Rollers &amp; Glides.com — Business Card</title>
<link rel="stylesheet" href="https://fonts.googleapis.com/css2?family=Montserrat:wght@700&family=Roboto:wght@400;500&family=Roboto+Condensed:wght@500&display=swap">
<style>
  :root {
    --brand-blue: #3461ac;
    --ink: #1d1d1f;
    --band-grey: #808285;
    --paper: #ffffff;
    --backdrop: #e9e7e3;
  }
  * { box-sizing: border-box; margin: 0; padding: 0; }
  html, body {
    width: 1200px; height: 900px; overflow: hidden;
    background: var(--backdrop);
  }
  .sheet {
    width: 1200px; height: 900px;
    display: flex; flex-direction: column;
    align-items: center; justify-content: center; gap: 40px;
  }
  .card {
    position: relative;
    width: 700px; height: 400px;
    overflow: hidden;
    box-shadow: 0 6px 18px rgba(0,0,0,0.18);
  }

  /* Front */
  .card--front {
    background: var(--brand-blue);
    display: flex; flex-direction: column;
    align-items: center; justify-content: center; gap: 34px;
  }
  .brand-dot {
    width: 92px; height: 92px; border-radius: 50%;
    background: var(--paper);
  }
  .brand-name--front {
    font-family: "Roboto", sans-serif;
    font-weight: 500;
    font-size: 40px;
    letter-spacing: 2px;
    color: var(--paper);
  }

  /* Back */
  .card--back { background: var(--paper); }
  .wave { position: absolute; inset: 0; width: 700px; height: 400px; }
  .holder {
    position: absolute; left: 58px; top: 58px;
  }
  .holder__name {
    font-family: "Montserrat", sans-serif;
    font-weight: 700; font-size: 25px;
    color: var(--brand-blue); text-transform: uppercase;
    letter-spacing: 0.3px; line-height: 1;
  }
  .holder__role {
    font-family: "Roboto", sans-serif;
    font-size: 19px; color: var(--ink); margin-top: 4px;
  }
  .brand-block {
    position: absolute; right: 44px; top: 34px;
    display: flex; flex-direction: column; align-items: center; gap: 16px;
  }
  .brand-dot--small {
    width: 70px; height: 70px; background: var(--brand-blue);
  }
  .brand-name--back {
    font-family: "Roboto Condensed", sans-serif;
    font-weight: 500; font-size: 27px; letter-spacing: 0.8px;
    color: var(--brand-blue); white-space: nowrap; line-height: 1.1;
  }
  .contact {
    position: absolute; left: 60px; top: 208px;
    list-style: none;
    font-family: "Roboto", sans-serif; font-size: 17px; color: var(--ink);
  }
  .contact__item {
    display: flex; align-items: center; gap: 10px; height: 25px;
  }
  .contact__icon { width: 17px; height: 17px; fill: var(--brand-blue); flex: none; }
  .contact__link { color: var(--brand-blue); }
</style>
</head>
<body>
<main class="sheet">

  <section class="card card--front" aria-label="Card front">
    <span class="brand-dot"></span>
    <p class="brand-name--front">Rollers &amp; Glides.com</p>
  </section>

  <section class="card card--back" aria-label="Card back">
    <svg class="wave" viewBox="0 0 700 400" aria-hidden="true">
      <path d="M0,326 C230,324 400,300 525,228 C410,304 240,342 0,344 Z" fill="var(--band-grey)"/>
      <path d="M0,352 C240,350 420,318 545,245 C615,204 662,180 700,172 L700,400 L0,400 Z" fill="var(--brand-blue)"/>
    </svg>

    <div class="holder">
      <h1 class="holder__name">Marcus Pellow</h1>
      <p class="holder__role">President</p>
    </div>

    <div class="brand-block">
      <span class="brand-dot brand-dot--small"></span>
      <p class="brand-name--back">Rollers &amp; Glides.com</p>
    </div>

    <ul class="contact">
      <li class="contact__item">
        <svg class="contact__icon" viewBox="0 0 24 24"><path d="M6.6 10.8a15.1 15.1 0 0 0 6.6 6.6l2.2-2.2a1 1 0 0 1 1-.25 11.4 11.4 0 0 0 3.6.57 1 1 0 0 1 1 1V20a1 1 0 0 1-1 1A17 17 0 0 1 3 4a1 1 0 0 1 1-1h3.5a1 1 0 0 1 1 1c0 1.25.2 2.450 .57 3.570a1 1 0 0 1-.25 1z"/></svg>
        <span>480.915.2267</span>
      </li>
      <li class="contact__item">
        <svg class="contact__icon" viewBox="0 0 24 24"><path d="M2 5h20v14H2z M2 5l10 8 10-8" fill="none" stroke="var(--brand-blue)" stroke-width="2"/></svg>
        <span>Marcus@rollersandglides-demo.com</span>
      </li>
      <li class="contact__item">
        <svg class="contact__icon" viewBox="0 0 24 24"><g fill="none" stroke="var(--brand-blue)" stroke-width="2"><circle cx="12" cy="12" r="9.5"/><path d="M2.5 12h19M12 2.5c3 3 3 16 0 19M12 2.5c-3 3-3 16 0 19"/></g></svg>
        <span>www.<span class="contact__link">rollersandglides-demo</span>.com</span>
      </li>
    </ul>
  </section>

</main>
</body>
</html>
```